Business card design for sustainable building and development company

Need a business card design for a new sustainable building and real estate development company in the San Francisco Bay area. Name of company is "Tovrin Advisors, LLC" and we provide "Sustainable building, energy and development services" for residential and non residential projects. We'd like the following colors used but not all area required: green, gray, blue. Design should communicate innovation, professionalism and sustainability. Our current website is www.tovrin-advisors.example. Another possible design idea is to have the following listed on the back of the card:
Certified: VERN QS, Eco Marker Rater, DOLM Rater, Terravue Inspector, KSO TQ Building Analyst. Its not a must but could be text that could be used for back of card. Overall, we are open to a simple, clean design and or one with more text than usual for a card.

Industry/Entity Type

Real Estate

Contact Information for Business Card

Name on card: Mark J. Halvik
Title for Name: Principal + Founder
Phone: 555.814.0627
Email: mhalvik@tovrin-advisors.example
Website: www.tovrin-advisors.example

Also, please add the following for address:
Lindenport, Calvera

Requirements
Nice to have
• If you can integrate the outline of a skyline on the backside of the card and if it looks good, I would like to see the design
Should not have
• a barcode;

```html
<!DOCTYPE html>
<html lang="en">
<head>
<meta charset="utf-8">
<title>Tovrin Advisors — Business Card</title>
<link rel="stylesheet" href="https://fonts.googleapis.com/css2?family=Montserrat:wght@700&family=Arimo:wght@400;700&display=swap">
<style>
  :root {
    --ink: #050505;
    --paper: #efefef;
    --green: #5bb335;
    --gray-text: #555555;
    --tagline: #cfcfcf;
    --stage: #d9d9d9;
  }
  * { box-sizing: border-box; margin: 0; padding: 0; }
  html, body { width: 1200px; height: 1029px; overflow: hidden; }
  body {
    background: var(--stage);
    font-family: "Arimo", Arial, sans-serif;
    position: relative;
  }
  .card {
    position: absolute;
    left: 250px;
    width: 700px;
    height: 400px;
    overflow: hidden;
    box-shadow: 0 6px 18px rgba(0,0,0,.25);
  }
  .card-back { top: 84px; background: var(--ink); }
  .card-front { top: 544px; background: var(--paper); }

  .brand {
    position: absolute;
    display: flex;
    align-items: center;
    gap: 18px;
  }
  .brand-mark {
    width: 92px; height: 92px;
    border-radius: 50%;
    background: var(--green);
    flex: none;
  }
  .brand-name {
    font-family: "Montserrat", Arial, sans-serif;
    font-weight: 700;
    font-size: 44px;
    color: var(--green);
    line-height: 1;
    white-space: nowrap;
  }
  .brand-tagline {
    font-size: 10.5px;
    letter-spacing: .3px;
    color: var(--tagline);
    text-transform: uppercase;
    margin-top: 6px;
    white-space: nowrap;
  }
  .card-back .brand { left: 150px; top: 108px; }

  .web-bar {
    position: absolute;
    right: 0; bottom: 62px;
    width: 300px; height: 30px;
    background: var(--green);
    color: #fff;
    font-size: 12px;
    font-weight: 700;
    letter-spacing: 1px;
    display: flex; align-items: center; justify-content: center;
    text-transform: uppercase;
  }

  .top-band {
    position: absolute;
    left: 0; top: 0;
    width: 100%; height: 175px;
    background: var(--ink);
  }
  .card-front .brand { left: 150px; top: 40px; }

  .contact-list {
    position: absolute;
    left: 44px; top: 212px;
    list-style: none;
  }
  .contact-list li {
    display: flex; align-items: center; gap: 14px;
    height: 30px;
    font-size: 14px;
    letter-spacing: 1px;
    color: var(--gray-text);
    text-transform: uppercase;
    white-space: nowrap;
  }
  .icon { width: 22px; height: 22px; flex: none; }

  .person {
    position: absolute;
    right: 34px; top: 272px;
    text-align: left;
  }
  .person-name {
    font-size: 24px;
    font-weight: 700;
    letter-spacing: 2px;
    color: var(--gray-text);
    text-transform: uppercase;
    white-space: nowrap;
  }
  .person-title {
    font-size: 15px;
    letter-spacing: 1.5px;
    color: var(--green);
    text-transform: uppercase;
    margin-top: 2px;
  }
</style>
</head>
<body>

<section class="card card-back">
  <div class="brand">
    <div class="brand-mark"></div>
    <div>
      <div class="brand-name">Tovrin Advisors</div>
      <div class="brand-tagline">Sustainable building, energy &amp; development services</div>
    </div>
  </div>
  <div class="web-bar">www.tovrin-advisors.example</div>
</section>

<section class="card card-front">
  <div class="top-band"></div>
  <div class="brand">
    <div class="brand-mark"></div>
    <div>
      <div class="brand-name">Tovrin Advisors</div>
      <div class="brand-tagline">Sustainable building, energy &amp; development services</div>
    </div>
  </div>

  <ul class="contact-list">
    <li>
      <svg class="icon" viewBox="0 0 22 22" aria-hidden="true"><rect width="22" height="22" rx="4" fill="#5bb335"/><rect x="7.5" y="4" width="7" height="14" rx="1.2" fill="none" stroke="#fff" stroke-width="1.4"/><circle cx="11" cy="15.5" r=".9" fill="#fff"/></svg>
      555.814.0627
    </li>
    <li>
      <svg class="icon" viewBox="0 0 22 22" aria-hidden="true"><rect width="22" height="22" rx="4" fill="#5bb335"/><rect x="4.5" y="6.5" width="13" height="9" fill="none" stroke="#fff" stroke-width="1.4"/><path d="M4.5 6.5 L11 12 L17.5 6.5" fill="none" stroke="#fff" stroke-width="1.4"/></svg>
      mhalvik@tovrin-advisors.example
    </li>
    <li>
      <svg class="icon" viewBox="0 0 22 22" aria-hidden="true"><rect width="22" height="22" rx="4" fill="#5bb335"/><circle cx="11" cy="11" r="6" fill="none" stroke="#fff" stroke-width="1.4"/><ellipse cx="11" cy="11" rx="2.6" ry="6" fill="none" stroke="#fff" stroke-width="1.2"/><path d="M5 11 H17" stroke="#fff" stroke-width="1.2"/></svg>
      www.tovrin-advisors.example
    </li>
    <li>
      <svg class="icon" viewBox="0 0 22 22" aria-hidden="true"><rect width="22" height="22" rx="4" fill="#5bb335"/><path d="M11 18 C7 13 6.5 11.5 6.5 9.5 A4.5 4.5 0 0 1 15.5 9.5 C15.5 11.5 15 13 11 18 Z" fill="#fff"/><circle cx="11" cy="9.5" r="1.7" fill="#5bb335"/></svg>
      Lindenport, Calvera
    </li>
  </ul>

  <div class="person">
    <div class="person-name">Mark J. Halvik</div>
    <div class="person-title">Principal/Owner</div>
  </div>
</section>

</body>
</html>
```